Business Card for a mobile physiotherapy company

I need a layout for a business card for a mobile physiotherapy company.
Slogan is "Mobile Physiotherapy - Your Road To Recovery"
Phone number is 867-555-0142
Email VardenTherapy@postnest.ca (subject to change with website)
Website www.VardenTherapy.ca
My name and credentials: Luke Varden Luke Varden, BSc(kin), MPT, CAFCI, IMS
Information maybe included: Direct Billing, Services including Physiotherapy, IMS, acupuncture
Maybe include facebook and instagram logos
One side with the logo clean and sharp
Other side with details, try not to look too busy, keep everything concise

```html
<!DOCTYPE html>
<html lang="en">
<head>
<meta charset="utf-8">
<title>Varden Therapy – Business Card</title>
<link href="https://fonts.googleapis.com/css2?family=Lora:wght@400;700&display=swap" rel="stylesheet">
<style>
  :root {
    --page-bg: #dcdad6;
    --card-light: #f3f2ef;
    --panel-top: #1d3a5c;
    --panel-bottom: #1c4e4c;
    --brand: #21506a;
    --gold: #d9c9a6;
    --soft-white: #e9ecee;
    --dot-a: #2f8fd0;
    --dot-b: #b23b86;
  }
  html, body {
    margin: 0;
    width: 1200px;
    height: 1054px;
    overflow: hidden;
    background: var(--page-bg);
  }
  .card {
    position: absolute;
    left: 100px;
    top: 227px;
    width: 1000px;
    height: 600px;
    background: var(--card-light);
    box-shadow: 0 10px 30px rgba(0,0,0,.18);
    overflow: hidden;
    font-family: "Lora", Georgia, serif;
  }
  .card__panel {
    position: absolute;
    inset: 0;
    width: 1000px;
    height: 600px;
  }
  .brand {
    position: absolute;
    left: 0;
    width: 470px;
    top: 270px;
    display: flex;
    align-items: center;
    justify-content: center;
    gap: 14px;
    color: var(--brand);
    font-size: 40px;
    font-weight: 400;
    line-height: 1;
  }
  .brand__mark {
    width: 30px;
    height: 30px;
    border-radius: 50%;
    background: var(--brand);
  }
  .details {
    position: absolute;
    left: 560px;
    top: 88px;
    color: var(--soft-white);
  }
  .details__name {
    font-size: 40px;
    font-weight: 700;
    color: var(--gold);
    letter-spacing: 1px;
    margin: 0;
  }
  .details__credentials {
    font-size: 21px;
    color: var(--gold);
    margin: 10px 0 0;
  }
  .social {
    display: flex;
    align-items: center;
    gap: 10px;
    margin-top: 48px;
    font-size: 24px;
    color: var(--gold);
  }
  .social__label { margin-right: 6px; }
  .social__dot {
    width: 38px;
    height: 38px;
    border-radius: 50%;
  }
  .social__dot--a { background: var(--dot-a); }
  .social__dot--b { background: var(--dot-b); }
  .contact {
    list-style: none;
    margin: 26px 0 0;
    padding: 0;
    font-size: 24px;
  }
  .contact__item {
    display: flex;
    align-items: center;
    height: 36px;
  }
  .contact__icon {
    width: 22px;
    height: 22px;
    margin-right: 28px;
    fill: none;
    stroke: var(--gold);
    stroke-width: 2;
  }
  .tagline {
    margin: 38px 0 0;
    font-size: 24px;
    line-height: 36px;
    color: var(--gold);
  }
</style>
</head>
<body>
  <div class="card">
    <svg class="card__panel" viewBox="0 0 1000 600" aria-hidden="true">
      <defs>
        <linearGradient id="panelGradient" x1="0" y1="0" x2="0" y2="1">
          <stop offset="0" stop-color="#1d3a5c"/>
          <stop offset="1" stop-color="#1c4e4c"/>
        </linearGradient>
      </defs>
      <path d="M420,0 Q560,300 410,600 L1000,600 L1000,0 Z" fill="url(#panelGradient)"/>
    </svg>

    <div class="brand">
      <span class="brand__mark"></span>
      <span class="brand__name">Varden Therapy</span>
    </div>

    <div class="details">
      <h1 class="details__name">LUKE VARDEN</h1>
      <p class="details__credentials">BSc(kin), MPT, CAFCI, IMS</p>

      <div class="social">
        <span class="social__label">Follow us on:</span>
        <span class="social__dot social__dot--a"></span>
        <span class="social__dot social__dot--b"></span>
      </div>

      <ul class="contact">
        <li class="contact__item">
          <svg class="contact__icon" viewBox="0 0 24 24"><path d="M4 9c0-3 16-3 16 0v2h-4V9H8v2H4z"/><rect x="6" y="12" width="12" height="8" rx="1"/></svg>
          867-555-0142
        </li>
        <li class="contact__item">
          <svg class="contact__icon" viewBox="0 0 24 24"><rect x="3" y="6" width="18" height="12"/><path d="M3 6l9 7 9-7"/></svg>
          VardenTherapy@postnest.ca
        </li>
        <li class="contact__item">
          <svg class="contact__icon" viewBox="0 0 24 24"><circle cx="12" cy="12" r="9"/><ellipse cx="12" cy="12" rx="4" ry="9"/><path d="M3 12h18"/></svg>
          www.VardenTherapy.ca
        </li>
      </ul>

      <p class="tagline">Mobile Physiotherapy<br>Your Road To Recovery</p>
    </div>
  </div>
</body>
</html>
```